Moldran Foods needs a new label for canned pineapple

We want a very tasty (in terms of making your mouth water) and clean design (less is more) for our canned pineapple under the new logo of Moldran Leafline division

Target Market(s)

The company’s mission is to bring quality food to target audiences of any social status (you receive a bit more than what you spend). Our core values are: reliability, loyalty and commitment to development.
The product is sold to mainstream and lower Mainstream customers.

Requirements
Must have
• The design should take into consideration the visibility on the shelf among competitor products (brief file) and that the product is a MAINSTREAM product.
We want a very tasty (in terms of making your mouth water) and clean design (less is more). The design should be easily modifiable for other canned fruits or vegetables.
The package must display on the front the following elements listed in the order of their should have noticeability:
• Moldran Leaf logo
• Pineapple picture
• Product name
Designers should take into account that the shelfs for displaying the products in the shops may have an elevation of up to 3 cm that can overlap the product label.

Guidelines
• We would like the packaging to be as simple as possible (or at least not to sabotage the Moldran name ), as our strategy depends on the agressive communication of the Moldran logo.
• We would also like to communicate through suggestive and optimal colours as to be easily spotted on the shelf.
• As we have quite a minimal communication budget we need basically for the packaging to do a lot of the communication job itself
• FMCG is a highly visual industry so we have to include pictures of the products on the packages (even more than others do, as we are focused on health and quality - we want people to have that feeling of fresh products even though we are selling canned ones)
Should not have
• but the minimum amount of text on the front.

```html
<!DOCTYPE html>
<html lang="ro">
<head>
<meta charset="utf-8">
<title>Moldran Leafline – Ananas, eticheta spate</title>
<link href="https://fonts.googleapis.com/css2?family=Roboto+Condensed:wght@400;700&family=Ubuntu:wght@400&display=swap" rel="stylesheet">
<style>
  :root {
    --bg: #f1f1f1;
    --label-top: #e6efb4;
    --label-mid: #bcdb6a;
    --label-bottom: #7fb238;
    --ink: #1f4a12;
    --table-bg: #0f4a1d;
    --table-ink: #f3e24a;
    --fruit-a: #c99a3a;
    --fruit-b: #5e8a3a;
  }
  * { box-sizing: border-box; margin: 0; padding: 0; }
  html, body { width: 1200px; height: 1200px; overflow: hidden; background: var(--bg); }
  .label {
    position: absolute; left: 265px; top: 170px; width: 640px; height: 860px;
    background: linear-gradient(180deg, var(--label-top) 0%, var(--label-mid) 45%, var(--label-bottom) 100%);
    font-family: "Roboto Condensed", sans-serif; color: var(--ink);
  }
  .fruit-visual {
    position: absolute; right: 0; top: 310px; width: 108px; height: 390px;
    background: linear-gradient(180deg, var(--fruit-b) 0%, var(--fruit-a) 70%, var(--fruit-b) 100%);
    border-radius: 54px 0 0 54px; opacity: .85;
  }
  .block { position: absolute; left: 0; width: 620px; text-align: center; }
  .heading { font-weight: 700; font-size: 25px; letter-spacing: .3px; }
  .line { font-size: 22px; line-height: 34px; }
  .ingredients { top: 58px; }
  .ingredients .line { font-size: 21px; margin-top: 4px; }
  .nutrition { top: 152px; }
  .nutrition .heading { margin-bottom: 8px; }
  .serving-title { top: 285px; }
  .serving { top: 683px; left: 0; width: 630px; }
  .serving .line { font-size: 22px; line-height: 35px; }
  .facts {
    position: absolute; left: 107px; top: 322px; width: 415px;
    background: var(--table-bg); color: var(--table-ink);
    font-family: "Ubuntu", sans-serif; font-size: 18px;
    border-collapse: collapse;
  }
  .facts td { border-top: 1px solid var(--table-ink); padding: 0 8px; vertical-align: top; line-height: 27px; }
  .facts td + td { border-left: 1px solid var(--table-ink); padding-left: 10px; }
  .facts tr:first-child td { border-top: none; }
  .facts .col-name { width: 256px; }
  .facts .col-amt { width: 89px; }
  .facts .pair td { padding-top: 2px; }
  .facts .gap { margin-left: 36px; }
  .facts .gap-sm { margin-left: 26px; }
</style>
</head>
<body>
  <main class="label">
    <div class="fruit-visual" role="img" aria-label="Fotografie cu un ananas proaspăt cu frunze verzi"></div>

    <section class="block ingredients">
      <h2 class="heading">INGREDIENTE</h2>
      <p class="line">Ananas(60.20%), Apă(31.7%), Zahăr(8%), Acid Citric(0.10%)</p>
    </section>

    <section class="block nutrition">
      <h2 class="heading">INFORMAȚII NUTRIȚIONALE</h2>
      <p class="line">O porție: ½ cană (140g)</p>
      <p class="line">Porții/cutie – aprox. 4</p>
    </section>

    <h2 class="block heading serving-title">CANTITATE/ PORȚIE</h2>

    <table class="facts">
      <tr><td colspan="3">Calorii 80<span class="gap">Acizi grași 0</span></td></tr>
      <tr class="pair"><td class="col-name">Lipide<br>Din care Lipide saturate</td><td class="col-amt">0g<br>0g</td><td>0%<br>0%</td></tr>
      <tr><td>Colesterol</td><td>0g</td><td>0%</td></tr>
      <tr><td>Sodiu</td><td>10mg</td><td>0%</td></tr>
      <tr><td>Carbohidrați<br>Fibre<br>Zaharuri</td><td>20g<br>&lt;1g<br>17g</td><td>6%<br>0%</td></tr>
      <tr><td>Proteine</td><td>0g</td><td></td></tr>
      <tr><td colspan="3">Vitamina A 0%<span class="gap-sm">Vitamina C 2%</span><span class="gap-sm">Calciu 2%</span><br>Fier 2%</td></tr>
    </table>

    <section class="block serving">
      <h2 class="heading">SUGESTIE DE SERVIRE</h2>
      <p class="line">A se servi simplu sau împreună cu prăjituri și produse de patiserie.</p>
      <p class="line">Poate servi pentru marinarea cărnii.</p>
      <p class="line">Perfect pentru piureuri din fructe.</p>
    </section>
  </main>
</body>
</html>
```